New Business Card Design for Manufacturing

We are an engineering/manufacturing company that offers Advanced machining/assembly/engineering services, as well as innovative products for the heavy duty engine cooling markets.

We are looking to get a new business card designed that is clean and modern looking, but still fits the wide range of technical/skilled work we do.

- We hope to use this design as the base for other design work in new Presentations, web, and print work.

Industry/Entity Type

Engineering

Contact Information for Business Card

Our preferred color of blue is (RGB) 22/71/159 but can vary slightly from that color. Our content will be our Logo and full company name (Vantrell Forge Works, Inc.), company address, name, job title, phone number with extension, cell number, fax number, website, and email address on the cards.
We'd like the full company name next to the logo, but we are open to other interpretations of that layout.
Preferably, we would like the back side to be clean with just our logo, and the front to contain all of the contact information.

Colors
2f74b4
0355a3
85abd2

Requirements
Must have
• - Logo, company name, needed content - We are open to interpretation beyond that.
• - Standard size business card.
• - Horizontal orientation.
• - Enough space for lengthy names / job titles (for example, a job title could read "Directory of Human Resources" or "V.P. of Governmental Affairs"). We need this to look clean, whether the title be short (CEO) or long (as described above).

```html
<!DOCTYPE html>
<html lang="en">
<head>
<meta charset="utf-8">
<title>Vantrell Forge Works – Business Card</title>
<link rel="stylesheet" href="https://fonts.googleapis.com/css2?family=Roboto:wght@400;500;700;900&display=swap">
<style>
  :root {
    --backdrop: #3a322d;
    --card: #1c1f24;
    --card-edge: #14161a;
    --brand-blue: #1f5fb8;
    --text-light: #e6e8eb;
    --text-muted: #9aa0a8;
    --silver: #cfd3d8;
    --divider: #4a4f57;
  }
  * { margin: 0; padding: 0; box-sizing: border-box; }
  html, body { width: 1200px; height: 769px; overflow: hidden; }
  body {
    background: var(--backdrop);
    font-family: "Roboto", sans-serif;
    position: relative;
  }
  .card {
    position: absolute;
    top: 236px;
    width: 520px;
    height: 297px;
    background: var(--card);
    border: 1px solid var(--card-edge);
    box-shadow: 0 18px 40px rgba(0,0,0,0.45);
  }
  .card--front { left: 50px; }
  .card--back { left: 630px; }

  /* front */
  .brand {
    position: absolute;
    left: 40px;
    top: 52px;
    display: flex;
    align-items: flex-start;
    gap: 22px;
  }
  .brand__mark {
    display: flex;
    flex-direction: column;
  }
  .brand__name {
    font-weight: 900;
    font-size: 40px;
    line-height: 1;
    color: var(--brand-blue);
    letter-spacing: 1px;
  }
  .brand__tagline {
    font-weight: 700;
    font-size: 12px;
    color: var(--text-muted);
    letter-spacing: 0.5px;
    margin-top: 6px;
  }
  .brand__company {
    font-weight: 900;
    font-size: 14px;
    line-height: 1.05;
    color: var(--brand-blue);
    letter-spacing: 0.5px;
    text-transform: uppercase;
    padding-top: 2px;
  }
  .brand__company small { font-size: 8px; }

  .person {
    position: absolute;
    right: 270px;
    top: 162px;
    text-align: right;
    white-space: nowrap;
  }
  .person__name {
    color: var(--brand-blue);
    font-weight: 500;
    font-size: 18px;
    text-transform: uppercase;
  }
  .person__title {
    color: var(--text-muted);
    font-size: 12.5px;
    margin-top: 3px;
  }
  .person__address {
    color: var(--text-light);
    font-size: 12.5px;
    line-height: 1.4;
    margin-top: 2px;
  }
  .divider {
    position: absolute;
    left: 262px;
    top: 158px;
    width: 1px;
    height: 92px;
    background: var(--divider);
  }
  .contact {
    position: absolute;
    left: 280px;
    top: 160px;
    list-style: none;
  }
  .contact li {
    display: flex;
    align-items: center;
    gap: 8px;
    color: var(--text-light);
    font-size: 12px;
    height: 21px;
  }
  .contact svg { width: 11px; height: 11px; fill: var(--brand-blue); flex: none; }

  /* back */
  .back-brand {
    position: absolute;
    left: 0; right: 0;
    top: 104px;
    text-align: center;
  }
  .back-brand__name {
    font-weight: 900;
    font-size: 54px;
    line-height: 1;
    color: var(--silver);
    letter-spacing: 2px;
  }
  .back-brand__tagline {
    font-weight: 700;
    font-size: 15px;
    color: var(--silver);
    letter-spacing: 1px;
    margin-top: 8px;
  }
</style>
</head>
<body>

<section class="card card--front" aria-label="Business card front">
  <div class="brand">
    <div class="brand__mark">
      <div class="brand__name">VANTRELL</div>
      <div class="brand__tagline">BUILT TO ENDURE</div>
    </div>
    <div class="brand__company">Vantrell<br>Forge<br>Works <small>Inc</small></div>
  </div>

  <div class="person">
    <div class="person__name">Dana Whitfield</div>
    <div class="person__title">V.P. of Governmental Affairs</div>
    <div class="person__address">2286 Larkspur Court<br>Anchorage, Alaska 99517</div>
  </div>

  <div class="divider"></div>

  <ul class="contact">
    <li>
      <svg viewBox="0 0 24 24" aria-hidden="true"><path d="M6.6 10.8a15.1 15.1 0 0 0 6.6 6.6l2.2-2.2a1 1 0 0 1 1-.25 11.4 11.4 0 0 0 3.6.57 1 1 0 0 1 1 1V20a1 1 0 0 1-1 1A17 17 0 0 1 3 4a1 1 0 0 1 1-1h3.5a1 1 0 0 1 1 1c0 1.25.2 2.45.57 3.57a1 1 0 0 1-.25 1z"/></svg>
      555 210 4471
    </li>
    <li>
      <svg viewBox="0 0 24 24" aria-hidden="true"><path d="M7 1h10a2 2 0 0 1 2 2v18a2 2 0 0 1-2 2H7a2 2 0 0 1-2-2V3a2 2 0 0 1 2-2zm0 3v14h10V4z"/></svg>
      555 318 9026
    </li>
    <li>
      <svg viewBox="0 0 24 24" aria-hidden="true"><path d="M2 5h20v14H2zm2 2v.5l8 5 8-5V7l-8 5z"/></svg>
      dana@vantrellforgeworks.com
    </li>
    <li>
      <svg viewBox="0 0 24 24" aria-hidden="true"><circle cx="12" cy="12" r="10"/></svg>
      www.vantrellforgeworks.com
    </li>
  </ul>
</section>

<section class="card card--back" aria-label="Business card back">
  <div class="back-brand">
    <div class="back-brand__name">VANTRELL</div>
    <div class="back-brand__tagline">BUILT TO ENDURE</div>
  </div>
</section>

</body>
</html>
```